Business Card Design

New business card design

Target Market(s)

Residential & Commercial Property Managers

Industry/Entity Type

Plumbing Services

Contact Information for Business Card

Name - Rowan Keddle, title - Director, Phone Number - 0431 286 517, email - rowan@tbk-plumbing.com.au, Company ABN - 73 215 904 386,

Font styles to use
Sans Serif

Colors
0054AA
0677BA
7BADD7
CADEEF
E8F1F8

```html
<!DOCTYPE html>
<html lang="en">
<head>
<meta charset="utf-8">
<title>TBK Plumbing – Business Card</title>
<link rel="stylesheet" href="https://fonts.googleapis.com/css2?family=Montserrat:wght@400;500;700&display=swap">
<style>
  :root {
    --page: #e9e6e1;
    --card-light: #ffffff;
    --card-dark: #1d232c;
    --ink: #1b1f24;
    --accent: #2ca7e0;
    --muted: #6f6a63;
  }
  * { margin: 0; padding: 0; box-sizing: border-box; }
  html, body { width: 900px; height: 1200px; overflow: hidden; }
  body {
    background: var(--page);
    font-family: "Montserrat", Arial, sans-serif;
    color: var(--ink);
    position: relative;
  }
  .card {
    position: absolute;
    border-radius: 22px;
    overflow: hidden;
    box-shadow: 0 6px 18px rgba(0,0,0,0.25);
  }
  .card-front { left: 80px; top: 130px; width: 742px; height: 442px; background: var(--card-light); }
  .card-back  { left: 78px; top: 638px; width: 744px; height: 440px; background: var(--card-dark); }

  .front-brand {
    position: absolute; left: 50px; top: 178px; width: 290px;
    display: flex; align-items: center; justify-content: center; gap: 12px;
    font-size: 38px; font-weight: 500; color: var(--ink); letter-spacing: 1px;
  }
  .brand-dot { width: 18px; height: 18px; border-radius: 50%; background: var(--accent); flex: none; }

  .divider { position: absolute; left: 368px; top: 138px; width: 2px; height: 182px; background: var(--ink); }

  .contact { position: absolute; left: 387px; top: 126px; }
  .contact-name { font-size: 25px; font-weight: 700; line-height: 30px; }
  .contact-title { font-size: 15px; font-weight: 500; margin-top: 1px; }
  .contact-list { list-style: none; margin-top: 19px; }
  .contact-list li { display: flex; align-items: center; gap: 11px; font-size: 15.5px; height: 30.5px; }
  .contact-list svg { width: 16px; height: 16px; fill: var(--ink); flex: none; }
  .contact-abn { font-size: 15.5px; margin-top: 0; }
  .contact-abn b { font-weight: 700; }

  .band-dark { position: absolute; left: 0; top: 388px; width: 625px; height: 32px; background: var(--card-dark); }
  .band-accent { position: absolute; left: 680px; top: 388px; width: 62px; height: 32px; background: var(--accent); }
  .band-mark {
    position: absolute; left: 624px; top: 371px; width: 62px; height: 62px; border-radius: 50%;
    background: var(--card-light); display: flex; align-items: center; justify-content: center;
  }
  .band-mark span { width: 44px; height: 44px; border-radius: 50%; background: var(--accent); }

  .back-brand {
    position: absolute; left: 0; right: 0; top: 170px;
    display: flex; align-items: center; justify-content: center; gap: 22px;
    font-size: 72px; font-weight: 500; color: #ffffff; letter-spacing: 2px;
  }
  .back-brand .brand-dot { width: 34px; height: 34px; }
</style>
</head>
<body>
  <section class="card card-front">
    <div class="front-brand"><span class="brand-dot"></span>TBK Plumbing</div>
    <div class="divider"></div>
    <div class="contact">
      <h1 class="contact-name">Rowan Keddle</h1>
      <p class="contact-title">Director</p>
      <ul class="contact-list">
        <li>
          <svg viewBox="0 0 24 24" aria-hidden="true"><path d="M6.6 10.8a15.1 15.1 0 0 0 6.6 6.6l2.2-2.2a1 1 0 0 1 1-.25 11.4 11.4 0 0 0 3.6.57 1 1 0 0 1 1 1V20a1 1 0 0 1-1 1A17 17 0 0 1 3 4a1 1 0 0 1 1-1h3.5a1 1 0 0 1 1 1c0 1.25.2 2.45.57 3.57a1 1 0 0 1-.25 1z"/></svg>
          0431 286 517
        </li>
        <li>
          <svg viewBox="0 0 24 24" aria-hidden="true"><path d="M3 5h18v14H3z M4 6.5v1l8 5 8-5v-1z" fill-rule="evenodd"/></svg>
          rowan@tbk-plumbing.com.au
        </li>
        <li>
          <svg viewBox="0 0 24 24" aria-hidden="true"><path d="M12 2a10 10 0 1 0 0 20 10 10 0 0 0 0-20zm0 2a8 8 0 0 1 7.4 5H15l-1 2-2-1-1 2 2 2v3l-2 2A8 8 0 0 1 4.3 10l3.7 1 2-3-2-3.3A8 8 0 0 1 12 4z"/></svg>
          www.tbk-plumbing.com.au
        </li>
      </ul>
      <p class="contact-abn"><b>ABN</b> - 73 215 904 386</p>
    </div>
    <div class="band-dark"></div>
    <div class="band-accent"></div>
    <div class="band-mark"><span></span></div>
  </section>

  <section class="card card-back">
    <div class="back-brand"><span class="brand-dot"></span>TBK Plumbing</div>
  </section>
</body>
</html>
```